Print materials for 3-star hotel

We are changing up our print materials (notepads, letterheads, key card jackets, small flyer for the room rates) We are a 3 star business hotel in the Philippines and have mainly used grey tones and clean, simple lines. See attached photos for logo and hotel interior photos.

Target Market(s)

Business

Contact Information for Business Card

Corvale Terrace Hotel
Lindwell Banca Avenue corner Tolenta St Cebu City 6000 Philippines
Tel: +63 32 481 7302
Mobile: +63 917 648 2095
www.corvaleterracehotel.example

Font styles to use
Serif
Sans Serif

Requirements
Must have
• Simple
• Readable font and font size
Nice to have
• Neutral colors, grey and taupes
Should not have
• No purples and bright blues

```html
<!DOCTYPE html>
<html lang="en">
<head>
<meta charset="utf-8">
<title>Corvale Terrace Hotel — Business Card</title>
<link href="https://fonts.googleapis.com/css2?family=Cinzel:wght@400&family=Cormorant+Garamond:wght@400;600&display=swap" rel="stylesheet">
<style>
  :root {
    --backdrop: #edf0f0;
    --card-grey: #aaa7a9;
    --card-shade: rgba(60, 60, 60, 0.18);
    --taupe-gold: #a58a63;
    --paper-white: #f7f7f6;
  }
  * { margin: 0; padding: 0; box-sizing: border-box; }
  html, body {
    width: 1200px;
    height: 900px;
    overflow: hidden;
    background: var(--backdrop);
  }
  .stage {
    position: relative;
    width: 1200px;
    height: 900px;
    display: flex;
    align-items: center;
    justify-content: center;
    gap: 56px;
  }
  .card {
    position: relative;
    width: 525px;
    height: 300px;
    background: var(--card-grey);
    box-shadow: 0 6px 18px var(--card-shade);
  }

  /* Front */
  .card-front {
    display: flex;
    flex-direction: column;
    align-items: center;
    justify-content: center;
    gap: 16px;
  }
  .brand-square {
    width: 34px;
    height: 34px;
    background: var(--taupe-gold);
  }
  .brand-name {
    font-family: "Cinzel", serif;
    font-weight: 400;
    font-size: 26px;
    letter-spacing: 0.22em;
    color: var(--taupe-gold);
    text-align: center;
    line-height: 1.35;
  }

  /* Back */
  .card-back {
    display: flex;
    align-items: center;
    padding: 0 40px 0 50px;
    gap: 38px;
  }
  .back-mark {
    display: flex;
    flex-direction: column;
    align-items: flex-start;
    gap: 12px;
    width: 150px;
  }
  .back-mark .brand-square {
    width: 64px;
    height: 64px;
    background: var(--paper-white);
  }
  .back-mark .brand-name {
    color: var(--paper-white);
    font-size: 17px;
    letter-spacing: 0.14em;
    text-align: left;
  }
  .contact {
    font-family: "Cormorant Garamond", serif;
    color: var(--paper-white);
    flex: 1;
  }
  .contact-name {
    font-size: 25px;
    letter-spacing: 0.04em;
    text-transform: uppercase;
    line-height: 1.1;
  }
  .contact-role {
    font-size: 16px;
    margin-top: 2px;
  }
  .contact-rule {
    width: 100%;
    height: 1.5px;
    background: var(--taupe-gold);
    margin: 16px 0 18px;
  }
  .contact-phone {
    font-size: 22px;
    font-weight: 600;
    letter-spacing: 0.02em;
  }
  .contact-line {
    font-size: 15px;
    line-height: 1.3;
  }
</style>
</head>
<body>
  <main class="stage">
    <section class="card card-front" aria-label="Business card front">
      <div class="brand-square" aria-hidden="true"></div>
      <h1 class="brand-name">Corvale Terrace<br>Hotel</h1>
    </section>

    <section class="card card-back" aria-label="Business card back">
      <div class="back-mark">
        <div class="brand-square" aria-hidden="true"></div>
        <p class="brand-name">Corvale Terrace Hotel</p>
      </div>
      <div class="contact">
        <p class="contact-name">Elias Navarro</p>
        <p class="contact-role">CEO/Founder</p>
        <div class="contact-rule" aria-hidden="true"></div>
        <p class="contact-phone">+63 917 648 2095</p>
        <p class="contact-line">elias@corvaleterracehotel.example</p>
        <p class="contact-line">www.corvaleterracehotel.example</p>
      </div>
    </section>
  </main>
</body>
</html>
```